Gobal construction supply company needs new business card design

I need a business card design for my global supply company using an existing logo. i will be looking to print these on rounded corner cards with the black background version of my logo on the back. on the front white background, my logo again and my simple details.

```html
<!DOCTYPE html>
<html lang="en">
<head>
<meta charset="utf-8">
<title>Meridian Supply Group – Business Cards</title>
<link href="https://fonts.googleapis.com/css2?family=Roboto:wght@400;500;700&display=swap" rel="stylesheet">
<style>
  :root {
    --backdrop: #3a3b3e;
    --card-black: #111111;
    --card-white: #ececec;
    --brand-red: #d7141a;
    --ink: #161616;
    --paper-text: #ffffff;
  }
  html, body {
    margin: 0;
    padding: 0;
    width: 1200px;
    height: 1000px;
    overflow: hidden;
    background: var(--backdrop);
    font-family: "Roboto", Arial, sans-serif;
  }
  .canvas {
    position: relative;
    width: 1200px;
    height: 1000px;
  }
  .card {
    position: absolute;
    width: 700px;
    height: 400px;
    border-radius: 34px;
    box-shadow: 0 18px 40px rgba(0,0,0,0.45);
    overflow: hidden;
  }
  .card--back {
    left: 420px;
    top: 60px;
    background: var(--card-black);
  }
  .card--front {
    left: 80px;
    top: 520px;
    background: var(--card-white);
  }
  .brand {
    position: absolute;
    font-weight: 700;
    letter-spacing: 0.02em;
    text-transform: uppercase;
    line-height: 1;
    white-space: nowrap;
  }
  .card--back .brand {
    left: 0;
    right: 0;
    top: 176px;
    text-align: center;
    font-size: 36px;
    color: var(--paper-text);
  }
  .card--front .brand {
    right: 56px;
    top: 92px;
    font-size: 27px;
    color: var(--ink);
  }
  .contact {
    position: absolute;
    left: 56px;
    top: 210px;
    color: var(--ink);
    font-size: 17px;
    line-height: 1.45;
  }
  .contact__name {
    color: var(--brand-red);
    font-weight: 700;
    font-size: 21px;
    text-transform: uppercase;
    margin: 0 0 6px;
  }
  .contact__title {
    color: var(--ink);
    font-weight: 400;
    font-size: 14px;
    text-transform: none;
    margin-left: 10px;
  }
  .contact__row { margin: 0; }
  .contact__label {
    color: var(--brand-red);
    font-weight: 700;
  }
  .contact__gap { margin-left: 14px; }
  .contact__domain {
    color: var(--brand-red);
    font-weight: 700;
  }
</style>
</head>
<body>
<main class="canvas">
  <section class="card card--back" aria-label="Card back">
    <div class="brand">Meridian Supply Group</div>
  </section>

  <section class="card card--front" aria-label="Card front">
    <div class="brand">Meridian Supply Group</div>
    <div class="contact">
      <p class="contact__name">Alex Morgan <span class="contact__title">Managing Director</span></p>
      <p class="contact__row"><span class="contact__label">cell:</span> +1 (555) 010 2040 <span class="contact__label contact__gap">office:</span> +1 (555) 010 2041</p>
      <p class="contact__row">alex@meridiansupply.com | www.<span class="contact__domain">meridiansupply</span>.com</p>
      <p class="contact__row">48 Harbor Street, Springfield, NY 10001</p>
    </div>
  </section>
</main>
</body>
</html>
```